WordPress Website Design for Multi-Brand Aviation Group (Unified Branding System)

Project Overview:
We are seeking a professional, modern WordPress website design for an aviation-focused umbrella company that owns and operates multiple subsidiary businesses. The goal is to create a cohesive visual system that clearly communicates that each company operates under the same parent organization, while still allowing each brand to maintain a slightly distinct identity.
This is not just a single website design—we are looking for a scalable design framework that can be applied across multiple aviation-related businesses.
Objectives:
- Establish a consistent, recognizable brand identity across all company websites
Clearly communicate the relationship between the parent company and its subsidiaries
-bCreate a clean, high-end corporate aviation aesthetic
- Ensure all designs are SEO-friendly and optimized for performance
- Allow flexibility for future expansion (additional subsidiaries)
- Target Audience:
- Corporate aviation clients
- Charter customers
- Students wishing to receive flight training
- Aircraft owners and operators
- Turbine aircraft training to meet insurance requirements
- Business professionals and high-net-worth individuals
- Aviation industry partners
Design Direction & Style:
We are looking for a premium, professional aviation feel—think clean, modern, and high-trust. The design should reflect the standards of corporate aviation: precision, safety, and sophistication.
Key style notes:
Minimalist but impactful layout
High-quality aviation photography (jets, interiors, operations, global travel)
Subtle motion/interaction (hover effects, transitions)
Clear typography hierarchy for readability and professionalism
Branding Requirements:
Incorporate the primary colors of the parent company logo across all designs
Website Structure (Core Pages):
Design a system that includes:
Home Page with the following links:
- About / Company Overview
- Aircraft Management
- Aircraft Acquisition
- Charter
- Pilot Services
- Trip Support
- Contact Page
Site should further include:
- Mobile-first responsive design
- Fast-loading, performance-optimized layouts
SEO & Technical Considerations:
- Design should support high-level SEO implementation:
- Clean layout structure that translates well to semantic HTML
- Proper heading hierarchy (H1, H2, H3)
- Space for keyword-rich content without clutter
- Optimized image placement (with alt text capability)
- Fast load times (lightweight design approach)
- Compatibility with WordPress SEO plugins (e.g., Yoast or Rank Math)
WordPress Requirements:
- Design should be easily built using WordPress (preferred builders: Elementor, Gutenberg, or similar)
- Reusable templates for scalability across multiple sites
- Easy for non-developers to update text and images
- Modular components (blocks/sections that can be reused across pages and sites)
- Navigation & UX:
- Simple, intuitive navigation
- Sticky header preferred
Style guide including:
- Colors
- Fonts
- Button styles
- Layout system
- Designs similar to high-end corporate aviation, private jet charter, or luxury service brands are preferred—clean, sharp, and premium without being overly flashy.
What We Want to Avoid:
- Overly busy layouts
- Generic templates with no brand identity
- Outdated or “stock” looking aviation designs
- Poor mobile responsiveness
Additional Notes:
We are building a long-term brand system, not just a one-off website. There is potential for ongoing work as we expand additional subsidiary sites.
We value designers who understand branding consistency across multiple business units and can create a scalable, professional system.
Include the attached main company logo "Vireton Aviation Group" and the "Member PJFO" logo on the main page.

```html
<!DOCTYPE html>
<html lang="en">
<head>
<meta charset="utf-8">
<title>Vireton Aviation Group</title>
<link href="https://fonts.googleapis.com/css2?family=Montserrat:wght@300;400;600;700;800&family=Roboto:wght@400;500;700&display=swap" rel="stylesheet">
<style>
:root{
  --cobalt:#0c4aa6;
  --cobalt-deep:#0a3d8f;
  --ink:#121212;
  --body:#3a3a3a;
  --muted:#5b5b5b;
  --mist:#f1f1f1;
  --line:#d9d9d9;
  --night:#161616;
  --white:#ffffff;
  --head:'Montserrat',sans-serif;
  --text:'Roboto',sans-serif;
}
*{margin:0;padding:0;box-sizing:border-box}
html,body{width:1200px;height:5089px;overflow:hidden}
body{font-family:var(--text);color:var(--ink);background:var(--white);position:relative}
section,header,footer,.topbar{position:relative;width:1200px}
a{color:inherit;text-decoration:none}
ul{list-style:none}
.brand{font-family:var(--head);font-weight:700;letter-spacing:.5px;color:var(--cobalt);line-height:1.1}
.brand small{display:block;font-size:10px;letter-spacing:2.6px;font-weight:700}
.dash{display:block;width:40px;height:4px;border-radius:2px;background:var(--ink)}
.dash.light{background:var(--white)}
.dash.center{margin:0 auto}
.btn{display:inline-flex;align-items:center;justify-content:center;height:40px;padding:0 28px;border-radius:4px;font:500 13px var(--text);background:var(--cobalt);color:var(--white)}
.btn.ghost{background:var(--white);color:var(--ink)}
.round-arrow{position:absolute;width:36px;height:36px;border-radius:50%;border:1px solid #9a9a9a;background:var(--white);display:flex;align-items:center;justify-content:center}
.round-arrow svg{width:12px;height:12px}

/* top bar */
.topbar{height:30px;background:#050505;color:var(--white);font-size:12.5px;font-weight:500}
.topbar::before{content:"";position:absolute;left:0;top:0;height:30px;width:605px;background:var(--cobalt);clip-path:polygon(0 0,100% 0,97% 100%,0 100%)}
.topbar .mail{position:absolute;left:105px;top:7px;display:flex;gap:8px;align-items:center}
.topbar .phone{position:absolute;left:948px;top:7px;display:flex;gap:8px;align-items:center}

/* header */
.site-header{height:82px;background:var(--white);border-bottom:1px solid #e6e6e6}
.site-header .brand{position:absolute;left:105px;top:22px;font-size:25px}
.site-header nav{position:absolute;left:322px;top:32px;display:flex;gap:30px;font:500 13px var(--text)}
.site-header nav .active{color:var(--cobalt)}
.site-header .btn{position:absolute;left:909px;top:20px;width:184px;padding:0}

/* hero */
.hero{height:641px;overflow:hidden}
.hero .sky{position:absolute;inset:0;background:linear-gradient(180deg,#2f6fb0 0%,#6c9fc9 30%,#d9b58c 62%,#e8c49a 78%,#c99f7e 100%)}
.hero h1{position:absolute;left:105px;top:118px;font:300 50px/1.12 var(--head);color:var(--ink)}
.hero h1 b{font-weight:800}
.hero p{position:absolute;left:105px;top:288px;width:420px;font-size:13.5px;line-height:1.75;color:var(--ink)}
.hero .actions{position:absolute;left:105px;top:392px;display:flex;gap:12px}
.hero .btn{height:40px;padding:0 28px}
.hero .round-arrow{top:550px}

/* intro */
.intro{height:409px;background:var(--mist)}
.intro h2{position:absolute;left:105px;top:90px;font:400 40px/1.2 var(--head)}
.intro h2 b{font-weight:800}
.intro .dash{position:absolute;left:115px;top:268px;width:120px;height:6px}
.intro .copy{position:absolute;left:578px;top:98px;width:478px;font-size:13.5px;line-height:1.75;color:var(--body)}
.intro .copy p+p{margin-top:22px}
.intro .btn{position:absolute;left:578px;top:256px}

/* services */
.services{height:881px}
.section-title{text-align:center;font:400 40px/1.2 var(--head)}
.section-title b{font-weight:800}
.services .dash{position:absolute;left:580px;top:96px}
.services .section-title{position:absolute;left:0;right:0;top:120px}
.cards{position:absolute;left:144px;top:243px;width:912px;display:grid;grid-template-columns:repeat(3,290px);gap:24px 21px}
.card{height:256px;background:var(--white);border-radius:16px;box-shadow:0 6px 24px rgba(0,0,0,.09);padding:32px 28px}
.card.featured{border-bottom:6px solid var(--cobalt)}
.card.featured h3{color:var(--cobalt)}
.card svg{width:58px;height:58px;display:block}
.card h3{margin-top:22px;font:700 17px var(--text)}
.card p{margin-top:10px;font-size:13.5px;line-height:1.75;color:var(--muted)}

/* strengths */
.strengths{height:767px;background:linear-gradient(160deg,#0b3f95 0%,#0c47a3 45%,#0a3c8d 100%);color:var(--white);overflow:hidden}
.strengths .haze{position:absolute;left:100px;top:210px;width:1000px;height:250px;background:radial-gradient(ellipse at center,rgba(140,170,220,.28),rgba(140,170,220,0) 70%)}
.strengths .dash{position:absolute;left:580px;top:92px}
.strengths .section-title{position:absolute;left:0;right:0;top:120px}
.hub{position:absolute;left:416px;top:273px;width:368px;height:368px;border-radius:50%;border:4px solid var(--white)}
.hub::before{content:"";position:absolute;inset:22px;border-radius:50%;border:14px solid var(--white)}
.hub::after{content:"";position:absolute;inset:60px;border-radius:50%;border:3px solid var(--white)}
.hub svg{position:absolute;left:134px;top:150px;width:100px;height:60px}
.trait{position:absolute;width:320px}
.trait h3{font:700 18px var(--text)}
.trait p{margin-top:8px;font-size:13.5px;line-height:1.7}
.trait .dot{position:absolute;top:-10px;width:88px;height:88px;border-radius:50%;background:var(--white);display:flex;align-items:center;justify-content:center}
.trait .dot svg{width:40px;height:40px}
.trait.left{text-align:right}
.trait.left .dot{right:-120px}
.trait.right .dot{left:-100px}

/* corporate */
.corporate{height:555px;overflow:hidden}
.corporate .sky{position:absolute;inset:0;background:linear-gradient(180deg,#5b8fc9 0%,#a9c4e3 45%,#dbe6f3 75%,#e8eef8 100%)}
.corporate .dash{position:absolute;left:580px;top:277px}
.corporate .section-title{position:absolute;left:0;right:0;top:300px;font-size:46px}
.corporate p{position:absolute;left:0;right:0;top:420px;text-align:center;font-size:15px;line-height:1.85;color:var(--body)}

/* audience */
.audience{height:607px}
.audience .dash{position:absolute;left:580px;top:103px}
.audience .section-title{position:absolute;left:0;right:0;top:125px}
.people{position:absolute;left:144px;top:210px;display:flex;gap:25px}
.person{width:209px;text-align:center}
.person .photo{height:278px;border-radius:10px}
.person h3{margin-top:22px;font:700 17px var(--text)}
.audience .round-arrow{top:343px}

/* industry */
.industry{height:308px}
.industry .rule{position:absolute;left:144px;top:0;width:911px;height:1px;background:var(--line)}
.industry .dash{position:absolute;left:144px;top:78px}
.industry h2{position:absolute;left:144px;top:102px;font:400 40px/1.2 var(--head)}
.industry h2 b{font-weight:800}
.industry p{position:absolute;left:144px;top:160px;width:440px;font-size:13.5px;line-height:1.75;color:var(--muted)}
.industry .brand{position:absolute;left:628px;top:148px;font-size:28px}
.member{position:absolute;left:850px;top:140px;display:flex;align-items:center;gap:10px}
.member .seal{width:56px;height:30px;border-radius:50%;background:var(--cobalt)}
.member span{font:400 10px var(--text);display:block}
.member strong{font:700 30px/1 var(--head);color:var(--ink);letter-spacing:2px}

/* cta */
.cta{height:363px;background:linear-gradient(180deg,#0c4aa6 0%,#0a3f92 100%);color:var(--white);text-align:center}
.cta .dash{position:absolute;left:580px;top:95px}
.cta h2{position:absolute;left:0;right:0;top:120px;font:400 40px/1.2 var(--head)}
.cta h2 b{font-weight:800}
.cta p{position:absolute;left:0;right:0;top:178px;font-size:14px}
.cta .actions{position:absolute;left:0;right:0;top:215px;display:flex;justify-content:center;gap:12px}
.cta .btn{color:var(--ink);background:var(--white);padding:0 24px}

/* footer */
.site-footer{height:446px;background:var(--night);color:#e8e8e8}
.site-footer .brand{position:absolute;left:142px;top:125px;font-size:29px;color:var(--white)}
.social{position:absolute;left:142px;top:196px;display:flex;gap:4px}
.social span{width:36px;height:36px;border-radius:50%;border:1.5px solid var(--white);display:flex;align-items:center;justify-content:center}
.social span::after{content:"";width:10px;height:10px;border-radius:50%;background:var(--white)}
.social span.on{background:var(--cobalt)}
.col{position:absolute;top:118px}
.col h4{font:700 18px var(--head);color:var(--white);letter-spacing:.5px}
.links{left:409px}
.links ul{margin-top:20px}
.links li{font-size:13px;line-height:24px;padding-left:24px;position:relative}
.links li::before{content:"";position:absolute;left:0;top:9px;width:6px;height:6px;border-radius:50%;background:var(--cobalt)}
.contact{left:585px;width:200px}
.contact dl{margin-top:20px;font-size:13px;line-height:21px}
.contact .item{position:relative;padding-left:24px;margin-bottom:22px}
.contact .item svg{position:absolute;left:0;top:4px;width:12px;height:12px}
.contact dt{font-weight:700}
.news{left:814px}
.news .field{margin-top:28px;font-size:13px;display:flex;align-items:center;gap:10px;padding-left:14px}
.news .btn{margin-top:20px;height:38px;font-size:13px;font-weight:700;padding:0 24px}
.copyright{position:absolute;left:0;right:0;bottom:12px;text-align:center;font-size:12.5px}
</style>
</head>
<body>

<div class="topbar">
  <span class="mail"><svg width="14" height="11" viewBox="0 0 14 11"><rect x="0.5" y="0.5" width="13" height="10" rx="1" fill="#fff"/><path d="M1 1l6 5 6-5" stroke="#0c4aa6" fill="none"/></svg>info@companyname.com</span>
  <span class="phone"><svg width="12" height="12" viewBox="0 0 24 24"><path fill="#fff" d="M6.6 10.8a15 15 0 006.6 6.6l2.2-2.2c.3-.3.7-.4 1-.2 1.1.4 2.3.6 3.6.6.6 0 1 .4 1 1V20c0 .6-.4 1-1 1A17 17 0 013 4c0-.6.4-1 1-1h3.5c.6 0 1 .4 1 1 0 1.3.2 2.5.6 3.6.1.3 0 .7-.2 1z"/></svg>+1 888 888 8888</span>
</div>

<header class="site-header">
  <div class="brand">VIRETON<small>AVIATION GROUP</small></div>
  <nav>
    <a class="active">Home</a><a>About</a><a>Aircraft Management</a><a>Pilot Services</a><a>Blog</a><a>Contact</a>
  </nav>
  <a class="btn">Request Consultation</a>
</header>

<section class="hero">
  <div class="sky" role="img" aria-label="Passenger jet flying above golden sunset clouds"></div>
  <h1>Elevating Aviation<br>Ownership, <b>Charter</b><br><b>Flight Solutions</b></h1>
  <p>Vireton Aviation Group delivers premium aviation services through a network of trusted subsidiaries specializing in aircraft management, charter, acquisitions, pilot services, and trip support.</p>
  <div class="actions"><a class="btn">Explore Services</a><a class="btn">Contact Us</a></div>
  <span class="round-arrow" style="left:104px"><svg viewBox="0 0 12 12"><path d="M8 1L3 6l5 5" stroke="#222" stroke-width="1.6" fill="none"/></svg></span>
  <span class="round-arrow" style="left:152px"><svg viewBox="0 0 12 12"><path d="M4 1l5 5-5 5" stroke="#222" stroke-width="1.6" fill="none"/></svg></span>
</section>

<section class="intro">
  <h2>One Aviation Group.<br><b>Multiple Specialized<br>Solutions.</b></h2>
  <span class="dash"></span>
  <div class="copy">
    <p>Vireton Aviation Group is a modern aviation holding company built to serve aircraft owners, charter clients, flight students, and aviation professionals through a unified network of specialized businesses.</p>
    <p>We combine operational excellence, safety, and premium service standards across every division.</p>
  </div>
  <a class="btn">Explore Services</a>
</section>

<section class="services">
  <span class="dash"></span>
  <h2 class="section-title">Our Aviation<br><b>Companies &amp; Services</b></h2>
  <div class="cards">
    <article class="card">
      <svg viewBox="0 0 58 58" fill="none" stroke="#0c4aa6" stroke-width="2"><circle cx="29" cy="29" r="24"/><circle cx="29" cy="29" r="15"/><path d="M22 30l5 5 10-11"/></svg>
      <h3>Aircraft Management</h3>
      <p>Professional oversight, operations, maintenance coordination, and owner support.</p>
    </article>
    <article class="card featured">
      <svg viewBox="0 0 58 58" fill="none" stroke="#0c4aa6" stroke-width="2"><path d="M6 22h40l6-6"/><path d="M20 22l8-10h6l-4 10"/><circle cx="29" cy="38" r="7"/><path d="M18 56c0-7 5-11 11-11s11 4 11 11"/></svg>
      <h3>Aircraft Acquisition</h3>
      <p>Strategic sourcing, evaluations, negotiations, and seamless ownership transitions.</p>
    </article>
    <article class="card">
      <svg viewBox="0 0 58 58" fill="none" stroke="#0c4aa6" stroke-width="2"><rect x="14" y="6" width="30" height="12" rx="3"/><path d="M4 36h46l6-8"/><path d="M20 36l10-12h6l-5 12"/><path d="M12 44l8 8"/></svg>
      <h3>Charter Services</h3>
      <p>Private charter solutions tailored for business and leisure travel.</p>
    </article>
    <article class="card">
      <svg viewBox="0 0 58 58" fill="none" stroke="#0c4aa6" stroke-width="2"><path d="M17 14h24l-3 8H20z"/><circle cx="29" cy="28" r="7"/><path d="M14 56V46c0-6 7-9 15-9s15 3 15 9v10"/><path d="M29 37v19"/></svg>
      <h3>Pilot Services</h3>
      <p>Experienced pilot staffing, training support, and flight crew solutions.</p>
    </article>
    <article class="card">
      <svg viewBox="0 0 58 58" fill="none" stroke="#0c4aa6" stroke-width="2"><circle cx="27" cy="31" r="21"/><path d="M6 31h42M27 10c-8 10-8 32 0 42M27 10c8 10 8 32 0 42"/><path d="M38 10l12-4-4 12"/></svg>
      <h3>Trip Support</h3>
      <p>Worldwide logistics, permits, scheduling, fuel, and concierge coordination.</p>
    </article>
    <article class="card">
      <svg viewBox="0 0 58 58" fill="none" stroke="#0c4aa6" stroke-width="2"><rect x="8" y="18" width="42" height="36"/><path d="M4 20L29 4l25 16"/><path d="M29 24v24M18 34h22M24 46h10"/></svg>
      <h3>Flight Training</h3>
      <p>Professional turbine and advanced aircraft training programs.</p>
    </article>
  </div>
</section>

<section class="strengths">
  <div class="haze" role="img" aria-label="Faint jet in flight over blue sky"></div>
  <span class="dash light"></span>
  <h2 class="section-title">Built for Owners.<br><b>Trusted by Professionals.</b></h2>
  <div class="hub"><svg viewBox="0 0 100 60"><path fill="#fff" d="M4 46l60-20 28-20c4-2 7 0 4 4L76 32 62 56h-6l6-20-30 10-8 8h-5l3-10z"/></svg></div>

  <div class="trait left" style="left:0;width:324px;top:2322px;margin-top:-2043px;left:0">
    <div class="dot" style="top:-10px"><svg viewBox="0 0 40 40" fill="none" stroke="#0c4aa6" stroke-width="2"><path d="M20 4l13 5v9c0 9-6 15-13 18C13 33 7 27 7 18V9z"/><path d="M14 20l4 4 8-8"/></svg></div>
    <h3>Safety First</h3>
    <p>Commitment to operational<br>discipline and industry best<br>practices.</p>
  </div>
  <div class="trait right" style="left:868px;top:279px">
    <div class="dot"><svg viewBox="0 0 40 40" fill="none" stroke="#0c4aa6" stroke-width="2"><circle cx="20" cy="20" r="7"/><path d="M20 4v6M20 30v6M4 20h6M30 20h6M9 9l4 4M27 27l4 4M31 9l-4 4M13 27l-4 4"/></svg></div>
    <h3>Industry Expertise</h3>
    <p>Experienced leadership<br>across aviation sectors.</p>
  </div>
  <div class="trait left" style="left:0;top:551px">
    <div class="dot"><svg viewBox="0 0 40 40" fill="none" stroke="#0c4aa6" stroke-width="2"><circle cx="20" cy="16" r="11"/><path d="M13 25l-4 12 11-5 11 5-4-12"/><path d="M16 16l3 3 6-6"/></svg></div>
    <h3>Premium Service</h3>
    <p>White-glove client experience<br>from inquiry to arrival.</p>
  </div>
  <div class="trait right" style="left:868px;top:551px">
    <div class="dot"><svg viewBox="0 0 40 40" fill="none" stroke="#0c4aa6" stroke-width="2"><path d="M20 6a10 10 0 00-6 18v5h12v-5a10 10 0 00-6-18z"/><path d="M15 33h10M17 37h6"/></svg></div>
    <h3>Scalable Solutions</h3>
    <p>Flexible support for<br>individuals, corporations,<br>and fleets.</p>
  </div>
</section>

<section class="corporate">
  <div class="sky" role="img" aria-label="Widebody jet approaching head-on against a pale blue sky"></div>
  <span class="dash"></span>
  <h2 class="section-title">Corporate Aviation<br><b>Without Compromise</b></h2>
  <p>From executive travel to aircraft ownership support, Vireton Aviation Group creates efficient, private,<br>and dependable aviation</p>
</section>

<section class="audience">
  <span class="dash"></span>
  <h2 class="section-title">Who <b>We Serve</b></h2>
  <span class="round-arrow" style="left:55px"><svg viewBox="0 0 12 12"><path d="M8 1L3 6l5 5" stroke="#222" stroke-width="1.6" fill="none"/></svg></span>
  <div class="people">
    <div class="person"><div class="photo" role="img" aria-label="Aircraft owner seated in a private jet cabin" style="background:linear-gradient(160deg,#6b4a36,#2c211b)"></div><h3>Aircraft Owners</h3></div>
    <div class="person"><div class="photo" role="img" aria-label="Traveller with backpack boarding a charter aircraft" style="background:linear-gradient(160deg,#dfe6ee,#8b99a7)"></div><h3>Charter Travelers</h3></div>
    <div class="person"><div class="photo" role="img" aria-label="Business executives talking in a terminal" style="background:linear-gradient(160deg,#9fb2c4,#3c4650)"></div><h3>Corporate Executives</h3></div>
    <div class="person"><div class="photo" role="img" aria-label="Flight students in a cockpit" style="background:linear-gradient(160deg,#3f5d7a,#121820)"></div><h3>Flight Students</h3></div>
  </div>
  <span class="round-arrow" style="left:1110px"><svg viewBox="0 0 12 12"><path d="M4 1l5 5-5 5" stroke="#222" stroke-width="1.6" fill="none"/></svg></span>
</section>

<section class="industry">
  <span class="rule"></span>
  <span class="dash"></span>
  <h2>Industry <b>Connected</b></h2>
  <p>Proudly aligned with leading aviation organizations and best practices.</p>
  <div class="brand">VIRETON<small>AVIATION GROUP</small></div>
  <div class="member"><span class="seal"></span><div><span>member of</span><strong>PJFO</strong></div></div>
</section>

<section class="cta">
  <span class="dash light"></span>
  <h2>Ready to Elevate <b>Your Aviation Experience?</b></h2>
  <p>Speak with our team about ownership, charter, management, or training solutions.</p>
  <div class="actions"><a class="btn">Contact Us</a><a class="btn">Schedule Consultation</a></div>
</section>

<footer class="site-footer">
  <div class="brand">VIRETON<small>AVIATION GROUP</small></div>
  <div class="social"><span></span><span class="on"></span><span></span></div>
  <div class="col links">
    <h4>QUICK LINKS</h4>
    <ul><li>About</li><li>Contact</li><li>Careers</li><li>Management</li><li>Charter</li><li>Acquisition</li><li>Pilot Services</li></ul>
  </div>
  <div class="col contact">
    <h4>CONTACT US</h4>
    <dl>
      <div class="item"><svg viewBox="0 0 12 12"><path fill="#0c4aa6" d="M6 0a4 4 0 00-4 4c0 3 4 8 4 8s4-5 4-8a4 4 0 00-4-4z"/></svg><dt>Address :</dt><dd>Lorem ipsum dolor sit amet, consectetur</dd></div>
      <div class="item"><svg viewBox="0 0 24 24"><path fill="#0c4aa6" d="M6.6 10.8a15 15 0 006.6 6.6l2.2-2.2c.3-.3.7-.4 1-.2 1.1.4 2.3.6 3.6.6.6 0 1 .4 1 1V20c0 .6-.4 1-1 1A17 17 0 013 4c0-.6.4-1 1-1h3.5c.6 0 1 .4 1 1 0 1.3.2 2.5.6 3.6.1.3 0 .7-.2 1z"/></svg><dt>Phone :</dt><dd>+1 888 888 8888</dd></div>
      <div class="item"><svg viewBox="0 0 12 12"><rect width="12" height="9" y="1.5" rx="1" fill="#0c4aa6"/></svg><dt>Email Address :</dt><dd>info@companyname.com</dd></div>
    </dl>
  </div>
  <div class="col news">
    <h4>OUR NEWSLETTER</h4>
    <div class="field"><svg width="13" height="10" viewBox="0 0 13 10"><rect width="13" height="10" rx="1" fill="#ddd"/><path d="M1 1l5.5 4.5L12 1" stroke="#161616" fill="none"/></svg>Email address</div>
    <a class="btn">SUBSCRIBE</a>
  </div>
  <p class="copyright">© Copyrights 2026 | All Rights Reserved</p>
</footer>

</body>
</html>
```